Storm Restoration Contractor needs a professional letterhead design

Looking for a professional letterhead design. Not looking for your cheapo MS Word standard ones that are readily available. Dont want it to be cookie cutter look like ones readily available online. We just recently changed our logo and want to freshen up all our documents. Our company handles restoring a property back to a pre-loss condition after a storm damages it. For example, wind, hail, flood, fire losses.

Target Market(s)

Property Owners, Homeowners, Property Owners, Commercial Property Owners, Property Management Companies

Industry/Entity Type

Construction Company

Requirements
Must have
• Professional, Use 1 of 2 logo options
• Storm Restoration, Roofing, Siding, Windows

```html
<!DOCTYPE html>
<html lang="en">
<head>
<meta charset="utf-8">
<title>Stormline Exteriors Letterhead</title>
<link rel="stylesheet" href="https://fonts.googleapis.com/css2?family=Open+Sans:wght@400;600;700&display=swap">
<style>
  :root {
    --brand-blue: #1f78c8;
    --ink: #3a3a3a;
    --ink-soft: #6b6b6b;
    --charcoal: #555759;
    --watermark: #eef2f8;
    --page: #ffffff;
    --backdrop: #ececec;
  }
  * { box-sizing: border-box; margin: 0; padding: 0; }
  html, body { width: 1200px; height: 795px; overflow: hidden; }
  body {
    background: var(--backdrop);
    font-family: "Open Sans", Arial, sans-serif;
    color: var(--ink);
  }
  .letterhead {
    position: absolute;
    left: 338px;
    top: 22px;
    width: 524px;
    height: 750px;
    background: var(--page);
    box-shadow: 0 2px 10px rgba(0,0,0,0.12);
    overflow: hidden;
  }
  .watermark {
    position: absolute;
    left: 150px;
    top: 150px;
    width: 300px;
    height: 300px;
  }
  .service-band {
    position: absolute;
    top: 0;
    right: 44px;
    width: 168px;
    height: 64px;
    background: var(--brand-blue);
    color: #fff;
    font-size: 6.5px;
    white-space: nowrap;
    padding: 0 10px 9px;
    display: flex;
    align-items: flex-end;
  }
  .brand {
    position: absolute;
    left: 42px;
    top: 150px;
    display: flex;
    align-items: center;
    gap: 8px;
  }
  .brand-dot {
    width: 26px;
    height: 26px;
    border-radius: 50%;
    background: var(--brand-blue);
  }
  .brand-name {
    font-size: 15px;
    font-weight: 700;
    color: var(--brand-blue);
    line-height: 1.05;
    letter-spacing: 1px;
    text-transform: uppercase;
  }
  .letter-body {
    position: absolute;
    left: 42px;
    top: 268px;
    width: 420px;
    font-size: 8.4px;
    line-height: 1.45;
    color: var(--ink-soft);
  }
  .salutation {
    font-weight: 700;
    font-size: 10px;
    color: var(--ink);
    margin-bottom: 10px;
  }
  .letter-body p { margin-bottom: 10px; }
  .signature {
    position: absolute;
    left: 42px;
    top: 500px;
    width: 110px;
    height: 40px;
  }
  .contact {
    position: absolute;
    right: 30px;
    top: 505px;
    text-align: right;
    font-style: normal;
    font-size: 7.5px;
    line-height: 1.55;
    color: var(--ink);
  }
  .social {
    display: flex;
    justify-content: flex-end;
    gap: 3px;
    margin-bottom: 2px;
  }
  .social span {
    width: 8px;
    height: 8px;
    border-radius: 50%;
    background: var(--brand-blue);
  }
  .footer-bar {
    position: absolute;
    right: 0;
    top: 580px;
    width: 170px;
    height: 14px;
    background: var(--charcoal);
  }
</style>
</head>
<body>
  <main class="letterhead">
    <svg class="watermark" viewBox="0 0 300 300" aria-hidden="true">
      <circle cx="150" cy="150" r="132" fill="none" stroke="var(--watermark)" stroke-width="22"/>
    </svg>

    <div class="service-band">Storm Restoration | Roofing | Siding | Windows</div>

    <div class="brand">
      <span class="brand-dot"></span>
      <span class="brand-name">Stormline<br>Exteriors</span>
    </div>

    <section class="letter-body">
      <p class="salutation">Dear Mr. Carter,</p>
      <p>Lorem Ipsum is simply dummy text of the printing and typesetting industry. Lorem Ipsum has been the industry's standard dummy text ever since the 1500s, when an unknown printer took a galley of type and scrambled it to make a type specimen book. It has survived not only five centuries, but also the leap into electronic typesetting, remaining essentially unchanged.</p>
      <p>The standard chunk of Lorem Ipsum used since the 1500s is reproduced below for those interested. Sections 1.10.32 and 1.10.33 from "de Finibus Bonorum et Malorum" by Cicero are also reproduced in their exact original form, accompanied by English versions from the 1914 translation by H. Rackham.</p>
      <p>Lorem Ipsum is simply dummy text of the printing and typesetting industry. Lorem Ipsum has been the industry's standard dummy text ever since the 1500s, when an unknown printer took a galley of type and scrambled it to make a type specimen book. It has survived not only five centuries, but also the leap into electronic typesetting, remaining essentially unchanged. It was popularised in the</p>
    </section>

    <svg class="signature" viewBox="0 0 110 40" role="img" aria-label="Handwritten signature of the sender">
      <rect x="0" y="0" width="110" height="40" rx="4" fill="#e6e6e6"/>
    </svg>

    <address class="contact">
      <div class="social"><span></span><span></span><span></span><span></span></div>
      555-201-4470<br>
      555-201-4471<br>
      info@stormlineexteriors.com<br>
      www.stormlineexteriors.com
    </address>

    <div class="footer-bar"></div>
  </main>
</body>
</html>
```